Creative, fresh business card design for Ripplecraft Facades

We need a fresh, creative business card design for Ripplecraft Facades. We are the manufacturer of Ripplecraft Facades in Australia. Wall panels are 2400 x 1200mm panels made from MDF and feature 3D patterns on the face of the panel. The colours to be used are green, silver/grey and white RGB
Red 187
Green 207
Blue 65.

An idea is to possibly use a watermark of one of our designs as a background (like on the "Grids" design on the left hand side of page 2 of our brochure).

Target Market(s)

Interior designers, architects, builders and home renovators

Industry/Entity Type

Business

Contact Information for Business Card

Details to go on the card are:
Our logo (attached),
Slogan: "Decorative panels for interiors and exteriors",
Contact name,
Position,
Mobile phone number,
Business address,
Business phone,
Business fax,
Website and
Email address.

I have attached a few images of our panels and our brochure for reference.

The colours of the business card should feature our logo colours which are: RGB
Red 187
Green 207
Blue 65

Requirements
Must have
• Very modern fonts and design. Some of the designs shown especially the "Prisms" design which is a popular design.
Nice to have
• Creative but simple design. Very contemporary.
Should not have
• Anything ornate or old fashioned.

```html
<!DOCTYPE html>
<html lang="en">
<head>
<meta charset="utf-8">
<title>Ripplecraft Facades – Business Card</title>
<link href="https://fonts.googleapis.com/css2?family=Arimo:ital,wght@0,400;0,700;1,400&display=swap" rel="stylesheet">
<style>
  :root {
    --green: rgb(187, 207, 65);
    --grey: #8c8d90;
    --grey-dark: #5f6062;
    --text: #3a3a3c;
    --white: #ffffff;
    --backdrop: #e9e9e7;
    --pattern-light: #f6f6f6;
    --pattern-mid: #e3e3e3;
  }
  * { box-sizing: border-box; margin: 0; padding: 0; }
  html, body {
    width: 1200px; height: 987px; overflow: hidden;
    background: var(--backdrop);
    font-family: "Arimo", Arial, sans-serif;
  }
  .canvas { position: relative; width: 1200px; height: 987px; }

  .card {
    position: absolute; left: 293px; width: 615px; height: 350px;
    background: var(--white); overflow: hidden;
    box-shadow: 0 2px 8px rgba(0,0,0,0.18);
  }
  .card-front { top: 131px; }
  .card-back { top: 506px; }

  /* front */
  .brand {
    position: absolute; right: 33px; top: 40px;
    display: flex; align-items: center; gap: 10px;
  }
  .brand-square { width: 34px; height: 34px; background: var(--green); }
  .brand-name { font-size: 25px; font-weight: 400; color: var(--grey-dark); }
  .tagline-front {
    position: absolute; right: 33px; top: 154px; text-align: right;
    font-size: 12px; line-height: 15px; letter-spacing: 2.6px; color: var(--grey);
  }
  .person-name {
    position: absolute; left: 29px; top: 172px;
    font-size: 23px; font-weight: 700; color: var(--green); letter-spacing: 0.3px;
  }
  .person-role {
    position: absolute; left: 29px; top: 201px; font-size: 17px; color: var(--grey);
  }
  .divider {
    position: absolute; left: 29px; right: 33px; top: 224px;
    height: 1px; background: var(--grey);
  }
  .contact-list {
    position: absolute; left: 33px; top: 240px; list-style: none;
  }
  .contact-list li {
    display: flex; align-items: center; gap: 8px;
    height: 23.5px; font-size: 16px; color: var(--text);
  }
  .contact-list svg { width: 13px; height: 13px; fill: var(--green); flex: none; }
  .address {
    position: absolute; right: 35px; top: 265px; text-align: right;
    font-size: 16px; line-height: 21px; color: var(--text);
  }
  .band-green {
    position: absolute; left: 0; bottom: 0; width: 340px; height: 14px;
    background: var(--green);
  }
  .band-web {
    position: absolute; right: 0; bottom: 0; width: 284px; height: 33px;
    background: var(--grey);
    clip-path: polygon(22px 0, 100% 0, 100% 100%, 0 100%);
    display: flex; align-items: center; justify-content: flex-end; padding-right: 18px;
    font-size: 14px; font-style: italic; letter-spacing: 1px; color: var(--white);
  }

  /* back */
  .panel-pattern {
    position: absolute; inset: 0;
    background: radial-gradient(circle at 35% 40%, var(--pattern-light), var(--pattern-mid));
  }
  .tagline-back {
    position: absolute; left: 0; width: 352px; top: 253px; text-align: right;
    font-size: 17px; line-height: 21px; letter-spacing: 3px; color: var(--grey);
  }
  .brand-back {
    position: absolute; right: 11px; top: 13px; bottom: 13px; width: 48px;
    background: var(--grey);
    display: flex; align-items: center; justify-content: center;
  }
  .brand-back .brand-name {
    transform: rotate(-90deg); white-space: nowrap;
    font-size: 25px; color: var(--white);
  }
  .brand-back-square {
    position: absolute; right: 67px; bottom: 13px; width: 48px; height: 48px;
    background: var(--green);
  }
</style>
</head>
<body>
<main class="canvas">

  <section class="card card-front" aria-label="Business card front">
    <div class="brand">
      <span class="brand-square"></span>
      <span class="brand-name">Ripplecraft Facades</span>
    </div>
    <p class="tagline-front">decorative panels for<br>interiors &amp; landscapes</p>

    <h1 class="person-name">MAREN HOLT</h1>
    <p class="person-role">CEO&amp;Founder</p>
    <div class="divider"></div>

    <ul class="contact-list">
      <li>
        <svg viewBox="0 0 16 16" aria-hidden="true"><path d="M3.5 1 6 3.8 4.6 5.6c.9 2 2.6 3.8 4.8 4.8l1.8-1.4L14 11.5 12.4 14C6.8 13.6 2.4 9.2 2 3.6z"/></svg>
        (555) 210-4738
      </li>
      <li>
        <svg viewBox="0 0 16 16" aria-hidden="true"><path d="M4 1h8v4H4zM1 6h14v6h-3v3H4v-3H1zm4 4v4h6v-4z"/></svg>
        (555) 210-4791
      </li>
      <li>
        <svg viewBox="0 0 16 16" aria-hidden="true"><path d="M1 3h14v10H1zm1.5 1.2L8 8.5l5.5-4.3z"/></svg>
        mholt@ripplecraftfacades.com
      </li>
    </ul>

    <p class="address">42 Fernhill Road<br>Geelong, Victoria 3220</p>

    <div class="band-green"></div>
    <div class="band-web">www.ripplecraftfacades.com</div>
  </section>

  <section class="card card-back" aria-label="Business card back">
    <div class="panel-pattern" role="img" aria-label="Faint white 3D prism wall panel pattern as background"></div>
    <p class="tagline-back">decorative panels for<br>interiors &amp; landscapes<br>www.ripplecraftfacades.com</p>
    <div class="brand-back-square"></div>
    <div class="brand-back"><span class="brand-name">Ripplecraft Facades</span></div>
  </section>

</main>
</body>
</html>
```